Real Estate stationery - need an interesting, eye catching design

I need a letterhead and #10 envelope design in the same theme.
I am looking for an interesting, eye catching design that would stand out in the crowd. I am in the real estate business(which is very competitive) in Florida so standing out and being different is very important to me.
Marguerite(Rita) Delacourt (name), RealtorĀ® (title), 352-608-2147 (cell), bayviewritahomes@quellmail.com (email), www.bayviewritahomes.com(website), 915 Calloway Creek Blvd.,Ste. 3140, Longwood, FL 32779 (business address)

```html
<!DOCTYPE html>
<html lang="en">
<head>
<meta charset="utf-8">
<title>Harborline Realty Stationery</title>
<link href="https://fonts.googleapis.com/css2?family=Didact+Gothic&family=Roboto:wght@400;500&display=swap" rel="stylesheet">
<style>
  :root {
    --brown: #76521f;
    --grey: #8b9098;
    --paper: #f7f7f7;
    --ink: #5a5a5a;
    --ink-soft: #6f6f6f;
    --backdrop: #e2e2e2;
  }
  html, body {
    margin: 0;
    padding: 0;
    width: 1200px;
    height: 843px;
    overflow: hidden;
    background: var(--backdrop);
  }
  .canvas {
    position: relative;
    width: 1200px;
    height: 843px;
  }
  .sheet {
    position: absolute;
    background: var(--paper);
    overflow: hidden;
  }
  .brand {
    font-family: "Didact Gothic", sans-serif;
    color: var(--brown);
    display: flex;
    align-items: center;
    gap: 6px;
    white-space: nowrap;
  }
  .brand-mark {
    width: 8px;
    height: 8px;
    background: var(--brown);
  }
  .footer-band {
    position: absolute;
    left: 0;
    bottom: 0;
    width: 100%;
    display: block;
  }

  /* Letterhead */
  .letterhead {
    left: 74px;
    top: 61px;
    width: 508px;
    height: 715px;
  }
  .letterhead .brand {
    position: absolute;
    top: 72px;
    left: 0;
    width: 100%;
    justify-content: center;
    font-size: 22px;
  }
  .salutation {
    position: absolute;
    left: 45px;
    top: 200px;
    margin: 0;
    font-family: "Didact Gothic", sans-serif;
    font-size: 13px;
    color: var(--ink);
  }
  .letter-body {
    position: absolute;
    left: 45px;
    top: 237px;
    width: 421px;
    font-family: "Didact Gothic", sans-serif;
    font-size: 7px;
    line-height: 11px;
    color: var(--ink-soft);
  }
  .letter-body p {
    margin: 0 0 11px;
  }
  .closing {
    position: absolute;
    left: 45px;
    top: 469px;
    margin: 0;
    font-family: "Didact Gothic", sans-serif;
    font-size: 7px;
    color: var(--ink-soft);
  }
  .signature {
    position: absolute;
    left: 39px;
    top: 498px;
    width: 92px;
    height: 38px;
    background: linear-gradient(90deg, rgba(118,82,31,0.18), rgba(118,82,31,0.08));
    border-radius: 3px;
  }
  .letter-footer {
    position: absolute;
    left: 0;
    top: 667px;
    width: 100%;
    text-align: center;
    font-family: "Roboto", sans-serif;
    font-size: 7px;
    line-height: 11px;
    color: var(--ink);
  }
  .letter-footer .label {
    color: var(--brown);
    font-weight: 500;
  }

  /* Envelope back */
  .envelope-back {
    left: 621px;
    top: 276px;
    width: 512px;
    height: 232px;
  }
  .flap {
    position: absolute;
    left: 0;
    top: 0;
    width: 512px;
    height: 72px;
    display: block;
  }
  .envelope-back .brand {
    position: absolute;
    top: 22px;
    left: 0;
    width: 100%;
    justify-content: center;
    color: #ffffff;
    font-size: 15px;
  }
  .envelope-back .brand-mark {
    background: #ffffff;
  }

  /* Envelope front */
  .envelope-front {
    left: 621px;
    top: 543px;
    width: 512px;
    height: 233px;
  }
  .envelope-front .brand {
    position: absolute;
    left: 25px;
    top: 36px;
    width: 114px;
    justify-content: center;
    font-size: 14px;
  }
  .return-address {
    position: absolute;
    left: 12px;
    top: 76px;
    width: 140px;
    text-align: center;
    font-family: "Roboto", sans-serif;
    font-size: 7px;
    line-height: 9px;
    color: var(--ink);
  }
</style>
</head>
<body>
<main class="canvas">

  <section class="sheet letterhead">
    <div class="brand"><span class="brand-mark"></span>Harborline Realty</div>

    <p class="salutation">Dear Mr. Alder,</p>

    <div class="letter-body">
      <p>Thank you for considering our team as you plan your next move in Central Florida. We know the local market well and will guide you through every step, from the first showing to the final signature at closing, with clear advice and steady care.</p>
      <p>Our listings are priced with care and marketed widely, so buyers notice them early. We host open houses on weekends, share fresh photos online, and answer every call the same day so that no good offer is ever missed or left waiting.</p>
      <p>When you are ready to buy, we will study each neighborhood with you, compare recent sales, and check schools, commutes and flood zones. Our goal is a home that fits your budget and your life, not just a house that looks good in photos.</p>
      <p>Please call or write any time with questions. We would be glad to meet for coffee and talk through your plans, your timeline and the options that make the most sense for you.</p>
    </div>

    <p class="closing">Sincerely,</p>
    <div class="signature" role="img" aria-label="Handwritten signature of Rita Delacourt"></div>

    <div class="letter-footer">
      <div>915 Calloway Creek Blvd., Ste. 3140, Longwood, FL 32779</div>
      <div><span class="label">M:</span> 352-608-2147 &nbsp;<span class="label">E:</span> bayviewritahomes@quellmail.com &nbsp;<span class="label">W:</span> www.bayviewritahomes.com</div>
    </div>

    <svg class="footer-band" width="508" height="9" viewBox="0 0 508 9" aria-hidden="true">
      <polygon points="0,0 415,0 411,9 0,9" fill="var(--brown)"/>
      <polygon points="417,0 508,0 508,9 413,9" fill="var(--grey)"/>
    </svg>
  </section>

  <section class="sheet envelope-back">
    <svg class="flap" viewBox="0 0 512 72" aria-hidden="true">
      <path d="M0,0 H512 V6 C508,40 500,72 470,72 H42 C12,72 4,40 0,6 Z" fill="var(--brown)"/>
    </svg>
    <div class="brand"><span class="brand-mark"></span>Harborline Realty</div>
  </section>

  <section class="sheet envelope-front">
    <div class="brand"><span class="brand-mark"></span>Harborline Realty</div>
    <div class="return-address">
      <div>915 Calloway Creek Blvd., Ste. 3140,</div>
      <div>Longwood, FL 32779</div>
    </div>
    <svg class="footer-band" width="512" height="9" viewBox="0 0 512 9" aria-hidden="true">
      <polygon points="0,0 388,0 384,9 0,9" fill="var(--brown)"/>
      <polygon points="390,0 512,0 512,9 386,9" fill="var(--grey)"/>
    </svg>
  </section>

</main>
</body>
</html>
```